UX Design for Analytics Web Application

http://velqoranthe.com/
We are tech & consulting company with analytics products (web applications), located at Rio de Janeiro, Brazil.

We are searching a partner do develop UX for our products, i.e, aesthetics, usability, HTML/CSS.

Currently we have a product suite and the goal is to make a pilot re-design project with one of our products.

The product of interest is interactive webapp that aims at data analysis, significantly different from blogs, e-commerce or landing pages.

We do have a software development team but we lack an UX & HTML expert. Currently we use Bootstrap templates but the results are insatisfatory.

So, the project scope is, to develop the arts (UX, aesthetics, etc) along with the code/mockup (HTML/CSS) for one of our product (3 pages).

This is a pilot project and there's potential to rehire for our other products. Code quality is of importance.

More details and specification can be found in attached files.

Target Market(s)

Executives, managers & consultants

Industry/Entity Type

It Company

Coding

Coded - Design and coding required

Number of Pages Required

3 page

Font styles to use
Sans Serif

Requirements
Must have
• (see attached files, prefer the pptx version))
• -Responsive
Nice to have
• (see attached files, prefer the pptx version)
Should not have
• -Avoid Green, Red and Yellow colors. They have a meaning of good, bad and average in our products.

```html
<!DOCTYPE html>
<html lang="en">
<head>
<meta charset="utf-8">
<title>Velqoranthe — Process Dashboard</title>
<link href="https://fonts.googleapis.com/css2?family=Open+Sans:wght@400;600;700&display=swap" rel="stylesheet">
<style>
:root{
  --bg:#f4f4f4;
  --white:#ffffff;
  --line:#dcdcdc;
  --text:#4a4a4a;
  --muted:#6b6b6b;
  --heading:#3c3c3c;
  --primary:#1e5f9e;
  --primary-dark:#173f6b;
  --accent:#5b4fc4;
  --accent-soft:#7fa7cf;
  --icon:#8a8a8a;
}
*{box-sizing:border-box;margin:0;padding:0}
html,body{width:1169px;height:1200px;overflow:hidden}
body{background:var(--bg);font-family:"Open Sans",Arial,sans-serif;color:var(--text);position:relative}

.topbar{position:absolute;left:0;top:0;width:1169px;height:97px;background:var(--white)}
.menu-btn{position:absolute;left:74px;top:38px}
.brand{position:absolute;left:133px;top:26px;display:flex;align-items:center;gap:12px}
.brand-dot{width:40px;height:40px;border-radius:50%;border:4px solid var(--heading)}
.brand-name{font-size:30px;font-weight:700;color:var(--heading);letter-spacing:.5px}
.top-icons{position:absolute;right:70px;top:37px;display:flex;gap:40px;align-items:center}
.bell{position:relative}
.badge{position:absolute;left:9px;top:-6px;width:15px;height:15px;border-radius:50%;background:var(--primary);color:#fff;font-size:9px;font-weight:700;display:flex;align-items:center;justify-content:center}

.panel{position:absolute;left:58px;width:1054px;background:var(--white);border:1px solid var(--line);border-radius:6px}
.overview{top:122px;height:298px}
.expenses{top:435px;height:694px}

.panel-title{position:absolute;left:16px;display:flex;align-items:center;gap:10px;font-size:18px;font-weight:600;color:var(--heading);letter-spacing:.6px}
.panel-title::after{content:"";position:absolute;left:0;top:37px;width:94px;height:3px;background:var(--line)}
.overview .panel-title{top:24px}
.expenses .panel-title{top:26px}
.dollar{color:var(--primary);font-size:22px;font-weight:600}

.stat{position:absolute;top:91px;width:235px;height:182px;border:1px solid var(--line);border-radius:5px;text-align:center}
.stat svg{display:block;margin:15px auto 0}
.stat-label{margin-top:14px;font-size:13.5px;font-weight:600;color:var(--muted);letter-spacing:.5px;line-height:19px;text-transform:uppercase}

.feed{position:absolute;left:765px;top:91px;width:274px;height:182px;background:#f2f2f2;border-radius:5px;padding:14px 16px}
.feed h3{font-size:16px;font-weight:600;color:var(--heading);letter-spacing:.5px;margin-bottom:7px}
.feed p{font-size:12.5px;line-height:18px;color:var(--muted)}
.feed .meta{font-size:12px;color:var(--primary);margin:3px 0 10px}

.btn-create{position:absolute;right:16px;top:22px;width:213px;height:46px;background:var(--primary);color:#fff;font-family:"Open Sans",Arial,sans-serif;font-size:14.5px;font-weight:700;letter-spacing:.6px;border:none;display:flex;align-items:center;justify-content:center}

.process-grid{position:absolute;left:15px;top:91px;display:grid;grid-template-columns:repeat(3,322px);column-gap:29px;row-gap:19px}
.process-card{height:250px;border:1px solid var(--line);border-radius:5px}
.process-card h4{height:58px;border-bottom:1px solid var(--line);padding:21px 19px 0;font-size:16.5px;font-weight:700;color:var(--primary);letter-spacing:.5px}
.process-body{padding:16px 19px 0}
.cost{display:flex;justify-content:space-between;font-size:14.5px;color:var(--text)}
.cost strong{color:var(--accent);font-weight:600}
.label{font-weight:700;color:var(--primary);font-size:14.5px;letter-spacing:.3px}
.status{margin-top:17px}
.status p{font-size:13.3px;line-height:20px;color:var(--muted);margin-top:5px;letter-spacing:.2px}
.stage{margin-top:10px;font-size:13.3px;color:var(--muted)}
.stage .label{margin-right:6px}

.pagination{position:absolute;left:488px;top:635px;display:flex;gap:7px}
.page{width:35px;height:35px;border:1px solid var(--line);display:flex;align-items:center;justify-content:center;font-size:15px;font-weight:700;color:var(--heading);background:#fff}
.page.active{background:var(--primary);border-color:var(--primary);color:#fff}

.footer{position:absolute;left:0;top:1158px;width:1169px;text-align:center;font-size:11px;color:var(--muted);letter-spacing:.4px}
</style>
</head>
<body>

<header class="topbar">
  <svg class="menu-btn" width="26" height="22" viewBox="0 0 26 22" aria-label="Menu">
    <rect y="0" width="26" height="3.5" fill="#6b6b6b"/><rect y="9" width="26" height="3.5" fill="#6b6b6b"/><rect y="18" width="26" height="3.5" fill="#6b6b6b"/>
  </svg>
  <div class="brand">
    <span class="brand-dot"></span>
    <span class="brand-name">Velqoranthe</span>
  </div>
  <div class="top-icons">
    <span class="bell">
      <svg width="18" height="20" viewBox="0 0 18 20"><path d="M9 1c-3.3 0-5.5 2.5-5.5 5.8v4.5L1.5 14v1.5h15V14l-2-2.7V6.8C14.5 3.5 12.3 1 9 1z" fill="var(--icon)"/><circle cx="9" cy="17.6" r="2" fill="var(--icon)"/></svg>
      <span class="badge">1</span>
    </span>
    <svg width="18" height="18" viewBox="0 0 18 18"><circle cx="9" cy="5" r="4.2" fill="var(--icon)"/><path d="M1 18c0-5 3.5-7.5 8-7.5s8 2.5 8 7.5z" fill="var(--icon)"/></svg>
    <svg width="19" height="19" viewBox="0 0 20 20"><path d="M10 0l1.6 2.7 3-.9.4 3.1 3 1-1.2 2.9L19 11l-2.7 1.6.9 3-3.1.4-1 3-2.9-1.2L8 19l-1.6-2.7-3 .9-.4-3.1-3-1 1.2-2.9L0 8l2.7-1.6-.9-3 3.1-.4 1-3 2.9 1.2z" fill="var(--icon)"/><circle cx="10" cy="10" r="3.2" fill="#fff"/></svg>
  </div>
</header>

<section class="panel overview">
  <h2 class="panel-title">
    <svg width="20" height="20" viewBox="0 0 20 20"><path d="M16 6.5A7 7 0 0 0 3.5 7.5" fill="none" stroke="var(--primary)" stroke-width="2.6"/><path d="M17.5 2v6h-6z" fill="var(--primary)"/><path d="M4 13.5A7 7 0 0 0 16.5 12.5" fill="none" stroke="var(--primary)" stroke-width="2.6"/><path d="M2.5 18v-6h6z" fill="var(--primary)"/></svg>
    PROCESS OVERVIEW
  </h2>

  <div class="stat" style="left:15px">
    <svg width="100" height="100" viewBox="0 0 100 100">
      <circle cx="50" cy="50" r="44" fill="none" stroke="#e2e2e2" stroke-width="1"/>
      <path d="M88 72 A44 44 0 0 1 50 94" fill="none" stroke="var(--accent-soft)" stroke-width="4"/>
      <text x="50" y="61" text-anchor="middle" font-family="Open Sans, sans-serif" font-size="30" font-weight="600" fill="#555">20</text>
    </svg>
    <div class="stat-label">Number of active<br>processes</div>
  </div>

  <div class="stat" style="left:264px">
    <svg width="100" height="100" viewBox="0 0 100 100">
      <circle cx="50" cy="50" r="44" fill="none" stroke="#e2e2e2" stroke-width="1"/>
      <path d="M6 50 A44 44 0 0 0 94 50" fill="none" stroke="var(--accent)" stroke-width="4"/>
      <text x="50" y="61" text-anchor="middle" font-family="Open Sans, sans-serif" font-size="30" font-weight="600" fill="#555">50</text>
    </svg>
    <div class="stat-label">Number of completed<br>processes</div>
  </div>

  <div class="stat" style="left:514px">
    <svg width="100" height="100" viewBox="0 0 100 100">
      <circle cx="50" cy="50" r="44" fill="none" stroke="#e2e2e2" stroke-width="1"/>
      <path d="M91 34 A44 44 0 1 1 9 34" fill="none" stroke="var(--primary)" stroke-width="4"/>
      <text x="50" y="61" text-anchor="middle" font-family="Open Sans, sans-serif" font-size="30" font-weight="600" fill="#555">72%</text>
    </svg>
    <div class="stat-label">Completion</div>
  </div>

  <aside class="feed">
    <h3>ACTIVITY FEED</h3>
    <p>Lorem ipsum dolor sit amet, consect aliquam erat volutpat..</p>
    <div class="meta">By Lena &nbsp;|&nbsp; Mar 30, 2017</div>
    <p>Lorem ipsum dolor sit amet, consect aliquam erat volutpat..</p>
    <div class="meta">By Lena &nbsp;|&nbsp; Mar 30, 2017</div>
  </aside>
</section>

<section class="panel expenses">
  <h2 class="panel-title"><span class="dollar">$</span> EXPENSES ($) OF ALL PROCESSES : $250</h2>
  <button class="btn-create">CREATE NEW PROCESS</button>

  <div class="process-grid">
    <article class="process-card"><h4>PROCESS NAME TITLE</h4><div class="process-body"><div class="cost"><span>Expenses ($) process cost:</span><strong>$20</strong></div><div class="status"><span class="label">Status:</span><p>Lorem ipsum dolor sit amet, consect- etuer adipiscing elit, sed diam nonummy nibh euismod sed diam ..</p></div><div class="stage"><span class="label">Current stage:</span> Executive Negotiation</div></div></article>
    <article class="process-card"><h4>PROCESS NAME TITLE</h4><div class="process-body"><div class="cost"><span>Expenses ($) process cost:</span><strong>$20</strong></div><div class="status"><span class="label">Status:</span><p>Lorem ipsum dolor sit amet, consect- etuer adipiscing elit, sed diam nonummy nibh euismod sed diam ..</p></div><div class="stage"><span class="label">Current stage:</span> Executive Negotiation</div></div></article>
    <article class="process-card"><h4>PROCESS NAME TITLE</h4><div class="process-body"><div class="cost"><span>Expenses ($) process cost:</span><strong>$20</strong></div><div class="status"><span class="label">Status:</span><p>Lorem ipsum dolor sit amet, consect- etuer adipiscing elit, sed diam nonummy nibh euismod sed diam ..</p></div><div class="stage"><span class="label">Current stage:</span> Executive Negotiation</div></div></article>
    <article class="process-card"><h4>PROCESS NAME TITLE</h4><div class="process-body"><div class="cost"><span>Expenses ($) process cost:</span><strong>$20</strong></div><div class="status"><span class="label">Status:</span><p>Lorem ipsum dolor sit amet, consect- etuer adipiscing elit, sed diam nonummy nibh euismod sed diam ..</p></div><div class="stage"><span class="label">Current stage:</span> Executive Negotiation</div></div></article>
    <article class="process-card"><h4>PROCESS NAME TITLE</h4><div class="process-body"><div class="cost"><span>Expenses ($) process cost:</span><strong>$20</strong></div><div class="status"><span class="label">Status:</span><p>Lorem ipsum dolor sit amet, consect- etuer adipiscing elit, sed diam nonummy nibh euismod sed diam ..</p></div><div class="stage"><span class="label">Current stage:</span> Executive Negotiation</div></div></article>
    <article class="process-card"><h4>PROCESS NAME TITLE</h4><div class="process-body"><div class="cost"><span>Expenses ($) process cost:</span><strong>$20</strong></div><div class="status"><span class="label">Status:</span><p>Lorem ipsum dolor sit amet, consect- etuer adipiscing elit, sed diam nonummy nibh euismod sed diam ..</p></div><div class="stage"><span class="label">Current stage:</span> Executive Negotiation</div></div></article>
  </div>

  <nav class="pagination">
    <span class="page active">1</span>
    <span class="page">2</span>
  </nav>
</section>

<footer class="footer">COPYRIGHT © 2017.ALL RIGHT RESERVED</footer>

</body>
</html>
```